Business Card: RW Office Partners - Your reliable everyday helper

Business Name: RW Office Partners
Website: www.rwofficepartners.com.au
Email: marisol@rwofficepartners.com.au
Mobile: 61 482 907 236
Facebook: @rwofficepartners
Instrgram: @rwofficepartners

Brading Colours:
HEX
#986474
#ddccd3
#7a8498
#c9d8e4
#000000
#ffffff

Tag Line: Your reliable everyday helper

Link to DRAFT website:
https://deskhelpcollective.wixsite.com/rw-office-partners

About Page from the website:
My name is Marisol Wrenfield, and I would love to assist you to become more productive in your day to day and achieve your business and personal goals.
My mission is to give you time, time to work on the important tasks of your business or to be able to spend more time with your family. I will take on the tasks you don’t have time for, don’t know well or simply don’t like to do.
I have an extensive background in Administration, Tender Coordination, Document Control, WHS and Quality Management working primarily in the Construction, Mining and Corporate World.
I am passionate about being organised, having order and making things in your life (and mine) easier! I love to watch something unfold and grow into something amazing! I am known for being the go-to problem solver, the organiser of all things, producing high standards of work even under pressure. I’m also a confident communicator, and I understand that you’re busy running your business.

Target Market(s)

Small to Medium Business who require assistance in their business by a virtual assistant.

Industry/Entity Type

Virtual Assistant

Contact Information for Business Card

Mobile: 61 482 907 236

Font styles to use
Sans Serif

Colors
ffffff

Requirements
Must have
• Branding Colours as outlined.
Contact Details as outlined.
Logo as provided.
Proper contact details - mobile, facebook, instragm, website.
Simple, Elegant, very clean looking.
Should not have
• Note cute with pictures.
Not too girly as still want to market to construction companies.

```html
<!DOCTYPE html>
<html lang="en">
<head>
<meta charset="utf-8">
<title>RW Office Partners – Business Card</title>
<link rel="stylesheet" href="https://fonts.googleapis.com/css2?family=Roboto:ital,wght@0,400;0,500;0,700;1,400&display=swap">
<style>
  :root {
    --backdrop: #3b3b3d;
    --card: #1d1b1f;
    --rose: #986474;
    --rose-light: #ddccd3;
    --slate: #7a8498;
    --slate-light: #c9d8e4;
    --ink-white: #ffffff;
    --tagline: #4a4650;
  }
  * { box-sizing: border-box; margin: 0; padding: 0; }
  html, body { width: 799px; height: 1200px; overflow: hidden; }
  body {
    background: var(--backdrop);
    font-family: "Roboto", Arial, sans-serif;
    display: flex;
    flex-direction: column;
    align-items: center;
    justify-content: center;
    gap: 90px;
  }
  .card {
    position: relative;
    width: 640px;
    height: 366px;
    background: var(--card);
    border-radius: 4px;
    box-shadow: 0 14px 30px rgba(0,0,0,0.45);
    color: var(--ink-white);
  }

  /* Brand name lockup */
  .brand {
    display: flex;
    align-items: center;
    font-weight: 500;
    text-transform: uppercase;
    letter-spacing: 0.04em;
    color: var(--slate);
    line-height: 0.95;
  }
  .brand-square { background: var(--rose); flex: none; }
  .brand-rule { background: var(--rose); width: 1px; align-self: stretch; flex: none; }

  /* Front */
  .card-front .brand {
    position: absolute;
    left: 160px;
    top: 92px;
    font-size: 42px;
    gap: 16px;
  }
  .card-front .brand-square { width: 64px; height: 64px; }
  .front-socials {
    position: absolute;
    left: 160px;
    top: 240px;
    display: flex;
    gap: 22px;
    font-size: 16px;
  }
  .social { display: flex; align-items: center; gap: 8px; }
  .social-mark {
    width: 12px; height: 12px;
    background: var(--rose);
    border-radius: 2px;
    flex: none;
  }

  /* Back */
  .card-back .brand-block {
    position: absolute;
    left: 40px;
    top: 106px;
  }
  .card-back .brand { font-size: 21px; gap: 8px; }
  .card-back .brand-square { width: 32px; height: 32px; }
  .tagline {
    margin-top: 8px;
    font-style: italic;
    font-size: 14px;
    color: var(--tagline);
    letter-spacing: 0.02em;
  }
  .contact-block {
    position: absolute;
    left: 345px;
    top: 104px;
  }
  .person-name {
    font-size: 22px;
    font-weight: 700;
    color: var(--rose);
  }
  .person-role {
    font-size: 15px;
    margin-top: 4px;
    margin-bottom: 18px;
  }
  .contact-list { list-style: none; font-size: 15px; }
  .contact-list li {
    display: flex;
    align-items: center;
    gap: 10px;
    height: 20px;
  }
  .contact-list svg { width: 12px; height: 12px; flex: none; }
</style>
</head>
<body>

  <section class="card card-front" aria-label="Card front">
    <div class="brand">
      <span class="brand-square"></span>
      <span class="brand-rule"></span>
      <span class="brand-name">RW Office<br>Partners</span>
    </div>
    <div class="front-socials">
      <span class="social"><span class="social-mark"></span>@rwofficepartners</span>
      <span class="social"><span class="social-mark"></span>@rwofficepartners</span>
    </div>
  </section>

  <section class="card card-back" aria-label="Card back">
    <div class="brand-block">
      <div class="brand">
        <span class="brand-square"></span>
        <span class="brand-rule"></span>
        <span class="brand-name">RW Office<br>Partners</span>
      </div>
      <p class="tagline">Your reliable everyday helper</p>
    </div>
    <div class="contact-block">
      <h1 class="person-name">Marisol Wrenfield</h1>
      <p class="person-role">Virtual Assistant</p>
      <ul class="contact-list">
        <li>
          <svg viewBox="0 0 12 12" aria-hidden="true"><path d="M2.5 1h2l1 3-1.3 1a6 6 0 0 0 2.8 2.8L8 6.5l3 1v2A1.5 1.5 0 0 1 9.5 11 8.5 8.5 0 0 1 1 2.5 1.5 1.5 0 0 1 2.5 1z" fill="#986474"/></svg>
          61 482 907 236
        </li>
        <li>
          <svg viewBox="0 0 12 12" aria-hidden="true"><rect x="0.5" y="2" width="11" height="8" fill="#986474"/><path d="M0.5 2 6 6.5 11.5 2" fill="none" stroke="#1d1b1f" stroke-width="1"/></svg>
          marisol@rwofficepartners.com.au
        </li>
        <li>
          <svg viewBox="0 0 12 12" aria-hidden="true"><g fill="none" stroke="#986474" stroke-width="1.2"><circle cx="6" cy="6" r="5"/><ellipse cx="6" cy="6" rx="2.2" ry="5"/><path d="M1 6h10"/></g></svg>
          www.rwofficepartners.com.au
        </li>
        <li><span class="social-mark"></span>@rwofficepartners</li>
        <li><span class="social-mark"></span>@rwofficepartners</li>
      </ul>
    </div>
  </section>

</body>
</html>
```